Locksmith Business Cards

My father-in-law is in need of new business cards for his locksmith business and I need to impress him. Kindly help me out!

You can see the previous business card attached. It is a family run business in North Wales.

No individual names on the cards.

Key Things to Feature:
- The words "Prompt", "Local", "Reliable" (as you can see under the logo on the website)
- 24h Emergency Service
- Covering All of North Wales, the Wirral and Chester
- The color blue
- A key or a lock would be interesting (similar to the ones that come up when you google locksmith business card)

Optional (only if design includes bullet points, like the example below):
https://imgvaultcdn.net/samples/208314/55172/55172_3904821_208314_image.jpg
- Residential / Commercial / Automotive
- Alarms & Cameras
- Key Cutting & Safes

https://www.brynhafod-locksmiths.co.uk/

Industry/Entity Type

Locksmith

Contact Information for Business Card

01632 960 418
07700 900 362
brynhafodlocksmiths@mailvane.com
Brynhafod Locksmiths, The Willow Barn, 7 Tannery Rd., Llandudno LL99 4QX
www.brynhafod-locksmiths.co.uk

Requirements
Must have
• - The words "Prompt", "Local", "Reliable" (as you can see under the logo on the website)
• - 24h Emergency Service
• - Covering All of North Wales, the Wirral and Chester
Nice to have
• - A key or a lock would be interesting (similar to the ones that come up when you google locksmith business card)

```html
<!DOCTYPE html>
<html lang="en">
<head>
<meta charset="utf-8">
<title>Brynhafod Locksmiths – Business Cards</title>
<link rel="stylesheet" href="https://fonts.googleapis.com/css2?family=Oswald:wght@500;600&family=Open+Sans:wght@400;700&display=swap">
<style>
  :root {
    --backdrop: #2a2a2c;
    --card: #ffffff;
    --navy: #1c2466;
    --blue: #4758a6;
    --ink: #3a3a3f;
    --rule: #c9cce0;
  }
  * { box-sizing: border-box; margin: 0; padding: 0; }
  html, body { width: 1200px; height: 900px; overflow: hidden; }
  body {
    background: var(--backdrop);
    font-family: "Open Sans", Arial, sans-serif;
    color: var(--ink);
    position: relative;
  }
  .card {
    position: absolute;
    left: 320px;
    width: 560px;
    height: 320px;
    background: var(--card);
    box-shadow: 0 10px 24px rgba(0,0,0,.45);
    text-align: center;
    overflow: hidden;
  }
  .card--front { top: 100px; }
  .card--back  { top: 480px; }

  .card__band {
    position: absolute;
    left: 0; right: 0; bottom: 0;
    height: 10px;
    display: flex;
  }
  .card__band-light { flex: 0 0 55%; background: var(--blue); }
  .card__band-dark  { flex: 1; background: var(--navy); }

  .brand {
    display: inline-flex;
    align-items: center;
    gap: 12px;
    margin-top: 34px;
  }
  .brand__mark {
    width: 22px; height: 22px;
    border-radius: 50%;
    background: var(--navy);
  }
  .brand__name {
    font-family: "Oswald", "Arial Narrow", sans-serif;
    font-weight: 600;
    font-size: 34px;
    line-height: 1;
    letter-spacing: .5px;
    text-transform: uppercase;
    color: var(--navy);
  }

  .services {
    margin-top: 20px;
    font-size: 14px;
    line-height: 1.3;
  }
  .rule {
    width: 300px;
    height: 1px;
    background: var(--rule);
    margin: 12px auto 10px;
  }
  .emergency {
    font-weight: 700;
    font-size: 14px;
    color: var(--navy);
    text-transform: uppercase;
  }
  .coverage { font-size: 14px; margin-top: 2px; }

  .tagline {
    font-family: "Oswald", "Arial Narrow", sans-serif;
    font-weight: 500;
    font-size: 17px;
    color: var(--navy);
    margin-top: 6px;
  }
  .contact {
    margin-top: 14px;
    font-size: 14px;
    line-height: 1.4;
  }
  .contact__label { font-weight: 700; color: var(--navy); }
  .contact__web { color: var(--blue); text-decoration: none; }
  .address { font-size: 14px; line-height: 1.35; }
</style>
</head>
<body>

  <section class="card card--front" aria-label="Business card front">
    <div class="brand">
      <span class="brand__mark"></span>
      <span class="brand__name">Brynhafod Locksmiths</span>
    </div>
    <p class="services">
      Residential / Commercial / Automotive<br>
      Alarms &amp; Cameras<br>
      Key Cutting &amp; Safes
    </p>
    <div class="rule"></div>
    <p class="emergency">24H Emergency Service</p>
    <p class="coverage">Covering All of North Wales, the Wirral and Chester</p>
    <div class="card__band"><span class="card__band-light"></span><span class="card__band-dark"></span></div>
  </section>

  <section class="card card--back" aria-label="Business card back">
    <div class="brand">
      <span class="brand__mark"></span>
      <span class="brand__name">Brynhafod Locksmiths</span>
    </div>
    <p class="tagline">Prompt. Local. Reliable</p>
    <p class="contact">
      <span class="contact__label">P:</span> 01632 960 418 | <span class="contact__label">M:</span> 07700 900 362<br>
      <span class="contact__label">E:</span> brynhafodlocksmiths@mailvane.com<br>
      <a class="contact__web" href="https://www.brynhafod-locksmiths.co.uk/">www.brynhafod-locksmiths.co.uk</a>
    </p>
    <div class="rule"></div>
    <p class="address">
      Brynhafod Locksmiths, The Willow Barn, 7<br>
      Tannery Rd., Llandudno LL99 4QX
    </p>
    <div class="card__band"><span class="card__band-light"></span><span class="card__band-dark"></span></div>
  </section>

</body>
</html>
```